Contemporary new French wine brand needs logo and series of label design

to design a new contemporary logo and series of labels for a new French wine brand. We hope to attract not just current French wine drinkers but new ones who may appreciate a less traditional and more modern style.
Updates

Reason: we are wanting to extend the project for a few days more to receive more submissions since we had fewer designs submitted than we were expecting, maybe because of the holidays.

Target Market(s)

people who follow the arts community (eg. music, theatre, visual/video arts, dance) --- all mature ages.

Industry/Entity Type

French Wine

Requirements
Must have
• a clear, memorable treatment for the name MORIVAL with accompanying logo.
Nice to have
• embossing, matte/gloss refinement, tasteful foil stamping, coated stock for the whites to help the integrity of the paper in and out of ice buckets. A combo of say, three types of fonts; a semi custom font for the brand name Morival and maybe a script and one other.
Should not have
• not traditional French

```html
<!DOCTYPE html>
<html lang="fr">
<head>
<meta charset="utf-8">
<title>Morival — Label Series</title>
<link rel="stylesheet" href="https://fonts.googleapis.com/css2?family=Josefin+Sans:wght@300&family=Cutive+Mono&family=Montserrat:wght@400&display=swap">
<style>
  :root {
    --canvas: #ffffff;
    --rose: #f0a498;
    --noir: #1d1c1b;
    --ink-light: #ffffff;
    --gold-dark: #9a6a1e;
    --gold-mid: #e0b865;
    --gold-light: #f6e2a8;
  }
  * { margin: 0; padding: 0; box-sizing: border-box; }
  html, body { width: 1200px; height: 1000px; overflow: hidden; background: var(--canvas); }
  .canvas { position: relative; width: 1200px; height: 1000px; }

  .label { position: absolute; color: var(--ink-light); }
  .label--rose { background: var(--rose); left: 125px; top: 428px; width: 253px; height: 378px; }
  .label--noir { background: var(--noir); left: 393px; top: 428px; width: 230px; height: 378px; }
  .label--feature { background: var(--noir); left: 786px; top: 309px; width: 303px; height: 497px; }

  .brand-mark {
    position: absolute; display: flex; flex-direction: column; align-items: center;
    font-family: "Josefin Sans", sans-serif; font-weight: 300; color: var(--ink-light);
    letter-spacing: 0.06em; line-height: 1;
  }
  .brand-mark__dot {
    border-radius: 50%; flex: none;
    background: radial-gradient(circle at 35% 35%, var(--gold-light), var(--gold-mid) 55%, var(--gold-dark));
  }

  .gold-rule {
    position: absolute; height: 2px;
    background: linear-gradient(90deg, var(--gold-dark), var(--gold-light) 45%, var(--gold-mid) 70%, var(--gold-dark));
  }
  .wine-name {
    position: absolute; font-family: "Josefin Sans", sans-serif; font-weight: 300;
    line-height: 1; letter-spacing: 0;
  }
  .wine-variety { position: absolute; font-family: "Cutive Mono", monospace; line-height: 1; white-space: nowrap; }
  .wine-region { position: absolute; font-family: "Montserrat", sans-serif; line-height: 1; letter-spacing: 0.06em; }

  /* small labels */
  .label--rose .brand-mark, .label--noir .brand-mark { top: 52px; width: 140px; font-size: 22px; gap: 16px; }
  .label--rose .brand-mark { left: 6px; }
  .label--noir .brand-mark { left: 8px; }
  .label--rose .brand-mark__dot, .label--noir .brand-mark__dot { width: 104px; height: 104px; }
  .label--rose .gold-rule, .label--noir .gold-rule { top: 266px; width: 140px; }
  .label--rose .gold-rule { left: 30px; }
  .label--noir .gold-rule { left: 31px; }
  .label--rose .wine-name, .label--noir .wine-name { top: 292px; font-size: 29px; }
  .label--rose .wine-name { left: 29px; }
  .label--noir .wine-name { left: 30px; }
  .label--rose .wine-variety, .label--noir .wine-variety { top: 322px; font-size: 15px; }
  .label--rose .wine-variety { left: 30px; }
  .label--noir .wine-variety { left: 31px; }
  .label--rose .wine-region, .label--noir .wine-region { top: 339px; font-size: 10.5px; }
  .label--rose .wine-region { left: 30px; }
  .label--noir .wine-region { left: 31px; }

  /* feature label */
  .label--feature .brand-mark { left: 4px; top: 64px; width: 190px; font-size: 30px; gap: 22px; }
  .label--feature .brand-mark__dot { width: 150px; height: 150px; }
  .label--feature .gold-rule { left: 40px; top: 350px; width: 185px; }
  .label--feature .wine-name { left: 40px; top: 386px; font-size: 40px; }
  .label--feature .wine-variety { left: 40px; top: 425px; font-size: 20px; }
  .label--feature .wine-region { left: 40px; top: 450px; font-size: 13px; }
</style>
</head>
<body>
<main class="canvas">
  <section class="label label--rose" aria-label="Étiquette rosé">
    <div class="brand-mark"><span class="brand-mark__dot"></span>MORIVAL</div>
    <div class="gold-rule"></div>
    <h2 class="wine-name">MORIVAL</h2>
    <p class="wine-variety">Rosè de Provence</p>
    <p class="wine-region">VAL DE LOIRE</p>
  </section>

  <section class="label label--noir" aria-label="Étiquette rouge">
    <div class="brand-mark"><span class="brand-mark__dot"></span>MORIVAL</div>
    <div class="gold-rule"></div>
    <h2 class="wine-name">MORIVAL</h2>
    <p class="wine-variety">Cabernet Sauvignon</p>
    <p class="wine-region">VAL DE LOIRE</p>
  </section>

  <section class="label label--feature" aria-label="Étiquette rouge, vue à plat">
    <div class="brand-mark"><span class="brand-mark__dot"></span>MORIVAL</div>
    <div class="gold-rule"></div>
    <h1 class="wine-name">MORIVAL</h1>
    <p class="wine-variety">Cabernet Sauvignon</p>
    <p class="wine-region">VAL DE LOIRE</p>
  </section>
</main>
</body>
</html>
```